Website for IT consulting Company

I need a website upgrade, the existing site content is ok, I would also like to add a testimonial page, the site should be something that is easy for us to update content. You use the content from www.kelvanbrook.com as an example. I will also post update logo and artwork. I also need a contact form with some type of validation or captcha.

I added Coded to the Project

Please omit Address maps

Target Market(s)

small business, service oriented companies. We provide IT Consulting, support and mangement

Industry/Entity Type

Information Technology

Coding

Number of Pages Required

1 page

Font styles to use
Serif
Sans Serif

Requirements
Must have
• Contain logo attached, and content from existing web site www.kelvanbrook.com.
• Also need to update content easily, and be movable to different platforms.
• There is a catch phrase
• "Let us worry about your technology…” “ so you don’t have to!”
• Should be included.
Nice to have
• Testimonial page, Project page where we can post new and past projects and pictures
Should not have
• none

```html
<!DOCTYPE html>
<html lang="en">
<head>
<meta charset="utf-8">
<title>Kelvanbrook Development Group – IT Consulting</title>
<link href="https://fonts.googleapis.com/css2?family=Open+Sans:wght@400;600;700&family=Raleway:wght@300;400;600;700&display=swap" rel="stylesheet">
<style>
:root{
  --blue:#1a8ad6;
  --blue-dark:#0f6fb5;
  --blue-deep:#0a2a55;
  --orange:#f27a1a;
  --ink:#333;
  --muted:#8a8a8a;
  --light:#f2f2f2;
  --white:#fff;
  --footer-top:#cfcfcf;
  --footer-bottom:#9d9d9d;
}
*{box-sizing:border-box;margin:0;padding:0}
html,body{width:1200px;height:3279px;overflow:hidden}
body{position:relative;font-family:"Open Sans",Arial,sans-serif;color:var(--ink);background:var(--white)}
.abs{position:absolute}
.btn{position:absolute;background:var(--blue);color:var(--white);font:700 15px "Open Sans",sans-serif;text-transform:uppercase;display:flex;align-items:center;justify-content:center;letter-spacing:.3px}

/* hero */
.hero{position:absolute;left:0;top:0;width:1200px;height:623px}
.hero-photo{position:absolute;inset:0;background:radial-gradient(ellipse at 62% 50%,#2f6fb8 0%,#123f7d 35%,#081b3c 75%,#050f25 100%)}
.brand{position:absolute;left:131px;top:34px;display:flex;align-items:center;gap:12px}
.brand-square{width:38px;height:38px;background:var(--orange)}
.brand-name{font:700 38px "Open Sans",sans-serif;color:var(--white);letter-spacing:1px}
.menu-toggle{position:absolute;left:962px;top:38px;display:flex;align-items:center;gap:10px;color:var(--white);font:400 17px "Open Sans",sans-serif}
.dropdown{position:absolute;left:848px;top:92px;width:219px;background:var(--blue)}
.dropdown li{list-style:none;height:38px;border-bottom:1px solid rgba(255,255,255,.35);color:var(--white);font:400 13px "Open Sans",sans-serif;padding:12px 0 0 26px;position:relative}
.dropdown li:last-child{border-bottom:none}
.dropdown .sub::after{content:"";position:absolute;right:16px;top:14px;width:8px;height:8px;border-top:2px solid #fff;border-right:2px solid #fff;transform:rotate(45deg)}
.hero-title{position:absolute;left:0;top:258px;width:1200px;text-align:center;color:var(--white);font:600 36px/40px "Raleway",sans-serif;letter-spacing:1px}
.hero .btn{left:450px;top:352px;width:304px;height:50px}
.dots{position:absolute;left:552px;top:581px;display:flex;gap:8px}
.dots span{width:13px;height:13px;border-radius:50%;background:var(--white)}
.dots span:first-child{background:transparent;border:2px solid var(--white)}

/* about */
.about{position:absolute;left:0;top:623px;width:1200px;height:420px;background:var(--white)}
.about-art{position:absolute;left:0;top:0;width:470px;height:420px;background:radial-gradient(circle at 45% 50%,#e6e6e6 0%,#b9b9b9 40%,#ffffff 75%)}
.about h2{position:absolute;left:540px;top:74px;font:400 30px "Raleway",sans-serif;color:#333}
.about p{position:absolute;left:540px;top:130px;width:540px;font:400 14px/22px "Open Sans",sans-serif;color:var(--muted)}
.about .btn{left:547px;top:310px;width:137px;height:37px;font-size:13px}

/* IT support */
.support{position:absolute;left:0;top:1043px;width:1200px;height:476px;background:linear-gradient(135deg,#1f9ae6 0%,#1478c6 60%,#1c8ad8 100%)}
.notch{position:absolute;left:570px;top:0;width:0;height:0;border-left:30px solid transparent;border-right:30px solid transparent;border-top:26px solid var(--white)}
.support h2{position:absolute;left:0;top:44px;width:1200px;text-align:center;color:var(--white);font:400 28px "Raleway",sans-serif}
.card{position:absolute;top:94px;width:300px;height:343px;background:var(--white);text-align:center}
.card-photo{height:168px}
.card h3{margin-top:18px;font:600 20px "Open Sans",sans-serif;color:var(--blue-dark)}
.card p{margin:10px 24px 0;font:400 12.5px/18px "Open Sans",sans-serif;color:var(--muted);height:54px;overflow:hidden}
.card .more{margin-top:12px;font:600 13px "Open Sans",sans-serif;color:var(--blue-dark)}
.card .more::after{content:"";display:block;width:30px;height:3px;background:var(--blue);margin:8px auto 0}

/* services */
.services{position:absolute;left:0;top:1519px;width:1200px;height:547px;background:var(--light);overflow:hidden}
.services h2{position:absolute;left:0;top:48px;width:1200px;text-align:center;font:400 24px "Raleway",sans-serif;color:#333}
.services svg{position:absolute;left:0;top:0}
.svc-label{font:400 12.5px "Open Sans",sans-serif;fill:#333;text-transform:uppercase}

/* testimonials */
.testimonials{position:absolute;left:0;top:2066px;width:1200px;height:332px;background:var(--white);border-top:1px solid #e2e2e2}
.testimonials h2{position:absolute;left:0;top:69px;width:1200px;text-align:center;font:400 24px "Raleway",sans-serif;color:var(--blue)}
.quote{position:absolute;left:240px;top:127px;width:720px;text-align:center;font:400 15px/24px "Open Sans",sans-serif;color:#555}
.quote b{color:var(--blue-dark);font:700 30px/0 "Raleway",sans-serif;vertical-align:-8px}
.author{position:absolute;left:0;top:232px;width:1200px;text-align:center;font:400 15px "Open Sans",sans-serif;color:#555}
.arrow{position:absolute;top:155px}

/* contact */
.contact{position:absolute;left:0;top:2398px;width:1200px;height:341px;background:#ececec}
.contact h2{position:absolute;left:0;top:60px;width:1200px;text-align:center;font:600 24px "Open Sans",sans-serif;color:var(--blue-dark)}
.field{position:absolute;background:var(--white);border:1px solid #d6d6d6;font:400 13px "Open Sans",sans-serif;color:#777;padding:11px 12px}
.contact .btn{left:538px;top:258px;width:135px;height:35px;font-size:13px}

/* partners */
.partners{position:absolute;left:0;top:2739px;width:1200px;height:164px;background:var(--white)}
.badge{position:absolute;top:58px;height:46px;background:#d9d9d9;border-radius:4px}

/* footer */
.footer{position:absolute;left:0;top:2903px;width:1200px;height:376px;background:linear-gradient(#d3d3d3,#9d9d9d)}
.fcol{position:absolute;top:62px;color:var(--white)}
.fcol h4{font:400 17px "Open Sans",sans-serif;text-transform:uppercase;margin-bottom:6px}
.fcol li{list-style:none;font:400 14px/27px "Open Sans",sans-serif}
.social{display:flex;gap:8px;margin-top:8px}
.social span{width:36px;height:36px;border-radius:50%;background:var(--blue)}
.social span:last-child{background:#d9493a}
.rule{position:absolute;left:153px;top:306px;width:907px;height:1px;background:rgba(255,255,255,.4)}
.copy{position:absolute;left:0;top:331px;width:1200px;text-align:center;color:var(--white);font:400 12px "Open Sans",sans-serif}
</style>
</head>
<body>

<header class="hero">
  <div class="hero-photo" role="img" aria-label="Photo of a hand touching a glowing blue touchscreen"></div>
  <div class="brand"><span class="brand-square"></span><span class="brand-name">KELVANBROOK</span></div>
  <div class="menu-toggle">
    <svg width="34" height="18" viewBox="0 0 34 18"><rect y="0" width="34" height="2.5" fill="#fff"/><rect y="7.5" width="34" height="2.5" fill="#fff"/><rect y="15" width="34" height="2.5" fill="#fff"/></svg>
    MENU
  </div>
  <ul class="dropdown">
    <li>HOME</li><li>ABOUT US</li><li>SUPPORT</li><li class="sub">SERVICES</li><li>PROJECTS</li><li>CONTACT</li>
  </ul>
  <h1 class="hero-title">FLEXIBLE SOLUTIONS FOR YOUR<br>BUSINESS NEEDS</h1>
  <div class="btn">Get a free IT assessment!</div>
  <div class="dots"><span></span><span></span><span></span><span></span></div>
</header>

<section class="about">
  <div class="about-art" role="img" aria-label="Illustration of a silver cube with orange blocks breaking away"></div>
  <h2>About Kelvanbrook Development Group, Inc</h2>
  <p>Kelvanbrook is a technology solution provider based in Houston, Texas. Our goal is to make technology a non-issue for individuals and small to medium size businesses ranging from 5 to 150 Users. Kelvanbrook has the experience, the tools, high-level technology solutions and training to power your business and your work force. We understand that all business's have one goal in common! (KDG) A Return on Investment</p>
  <div class="btn">Read more</div>
</section>

<section class="support">
  <div class="notch"></div>
  <h2>IT SUPPORT SOLUTIONS</h2>
  <article class="card" style="left:131px">
    <div class="card-photo" role="img" aria-label="Photo of hands using a tablet with network graphics" style="background:linear-gradient(135deg,#1c3b5e,#3f7fb0)"></div>
    <h3>Managed IT Solutions</h3>
    <p>Our staff will design, service, administer and maintain your IT needs. We are well versed on all major operating system, and</p>
    <div class="more">LEARN MORE</div>
  </article>
  <article class="card" style="left:448px">
    <div class="card-photo" role="img" aria-label="Photo of technicians working in a server room" style="background:linear-gradient(135deg,#2a4a5e,#6f93a8)"></div>
    <h3>Remote Diagnostic</h3>
    <p>Do you need a quick solution to a technical problem? With our live remote-assistance tool, a member of our support team can</p>
    <div class="more">LEARN MORE</div>
  </article>
  <article class="card" style="left:765px">
    <div class="card-photo" role="img" aria-label="Photo of an engineer beside server racks" style="background:linear-gradient(135deg,#8a9aa6,#d5dde2)"></div>
    <h3>IT Infrastructure Design</h3>
    <p>Do you have more than one site? Do you need remote access? We can design and implement LANS/WANS and VPN's.</p>
    <div class="more">LEARN MORE</div>
  </article>
</section>

<section class="services">
  <h2>OUR SERVICES</h2>
  <svg width="1200" height="547" viewBox="0 0 1200 547">
    <g stroke="#1a8ad6" stroke-width="3">
      <line x1="603" y1="560" x2="236" y2="488"/>
      <line x1="603" y1="560" x2="254" y2="387"/>
      <line x1="603" y1="560" x2="304" y2="287"/>
      <line x1="603" y1="560" x2="407" y2="201"/>
      <line x1="603" y1="560" x2="529" y2="151"/>
      <line x1="603" y1="560" x2="662" y2="149"/>
      <line x1="603" y1="560" x2="780" y2="193"/>
      <line x1="603" y1="560" x2="890" y2="280"/>
      <line x1="603" y1="560" x2="951" y2="385"/>
      <line x1="603" y1="560" x2="975" y2="481"/>
      <line x1="603" y1="560" x2="330" y2="507"/>
      <line x1="603" y1="560" x2="876" y2="507"/>
      <line x1="603" y1="560" x2="603" y2="270"/>
    </g>
    <g fill="#1a8ad6">
      <circle cx="330" cy="507" r="6"/><circle cx="876" cy="507" r="6"/><circle cx="603" cy="270" r="6"/>
      <circle cx="348" cy="430" r="6"/><circle cx="858" cy="430" r="6"/><circle cx="400" cy="350" r="6"/><circle cx="806" cy="350" r="6"/>
    </g>
    <circle cx="603" cy="560" r="212" fill="#1a8ad6"/>
    <circle cx="603" cy="560" r="168" fill="#e8e8e8"/>
    <circle cx="603" cy="560" r="156" fill="#ffffff"/>
    <rect x="478" y="466" width="22" height="22" fill="#f27a1a"/>
    <text x="508" y="486" font-family="Open Sans, sans-serif" font-weight="700" font-size="24" fill="#7a7a7a">KELVANBROOK</text>

    <g stroke="#fff" stroke-width="3" fill="#1a8ad6">
      <circle cx="236" cy="488" r="40"/><circle cx="254" cy="387" r="40"/><circle cx="304" cy="287" r="40"/>
      <circle cx="407" cy="201" r="40"/><circle cx="529" cy="151" r="40"/><circle cx="662" cy="149" r="40"/>
      <circle cx="780" cy="193" r="40"/><circle cx="890" cy="280" r="40"/><circle cx="951" cy="385" r="40"/><circle cx="975" cy="481" r="40"/>
    </g>
    <g fill="none" stroke="#fff" stroke-width="3">
      <circle cx="236" cy="488" r="9"/><circle cx="236" cy="488" r="16" stroke-dasharray="6 4"/>
      <circle cx="254" cy="387" r="15"/><line x1="239" y1="387" x2="269" y2="387"/><ellipse cx="254" cy="387" rx="6" ry="15"/>
      <line x1="304" y1="275" x2="304" y2="303"/><path d="M296 303 L304 280 L312 303"/><path d="M294 276 a14 14 0 0 1 20 0"/>
      <rect x="393" y="192" width="20" height="18" fill="#fff"/><path d="M413 197 L424 191 L424 211 L413 205Z" fill="#fff"/>
      <circle cx="529" cy="151" r="14"/><line x1="529" y1="137" x2="529" y2="165"/><line x1="515" y1="151" x2="543" y2="151"/>
      <rect x="648" y="138" width="28" height="19" rx="2"/><line x1="656" y1="163" x2="668" y2="163"/>
      <circle cx="770" cy="185" r="4"/><circle cx="792" cy="185" r="4"/><circle cx="780" cy="204" r="4"/><path d="M773 188 L778 200 M789 188 L783 200 M774 185 H788"/>
      <path d="M874 276 a22 22 0 0 1 32 0"/><path d="M880 283 a14 14 0 0 1 20 0"/><circle cx="890" cy="291" r="3" fill="#fff"/>
      <path d="M951 368 L966 374 V386 C966 396 958 402 951 405 C944 402 936 396 936 386 V374Z"/>
      <path d="M962 492 H990 a8 8 0 0 0 0-16 a12 12 0 0 0-23-3 a9 9 0 0 0-5 19Z"/>
    </g>
    <text class="svc-label" x="184" y="484" text-anchor="end">Desktop</text><text class="svc-label" x="184" y="500" text-anchor="end">Support</text>
    <text class="svc-label" x="208" y="383" text-anchor="end">Network</text><text class="svc-label" x="208" y="399" text-anchor="end">Administration</text>
    <text class="svc-label" x="258" y="292" text-anchor="end">Telecommunication</text>
    <text class="svc-label" x="356" y="196" text-anchor="end">Audio/Video</text><text class="svc-label" x="356" y="212" text-anchor="end">Multimedia</text>
    <text class="svc-label" x="487" y="126" text-anchor="end">Disaster</text><text class="svc-label" x="487" y="142" text-anchor="end">Recovery</text>
    <text class="svc-label" x="712" y="136">Webdesign</text>
    <text class="svc-label" x="838" y="182">Network</text><text class="svc-label" x="838" y="198">Cabling</text>
    <text class="svc-label" x="946" y="269">Wireless</text><text class="svc-label" x="946" y="285">Networks</text>
    <text class="svc-label" x="1003" y="374">Antivirus</text><text class="svc-label" x="1003" y="390">Solution</text>
    <text class="svc-label" x="1025" y="478">Cloud Hosting</text><text class="svc-label" x="1025" y="494">\Virtualization</text>
  </svg>
</section>

<section class="testimonials">
  <h2>TESTIMONIALS</h2>
  <svg class="arrow" style="left:140px" width="26" height="56" viewBox="0 0 26 56"><path d="M24 2 L3 28 L24 54" fill="none" stroke="#777" stroke-width="2"/></svg>
  <svg class="arrow" style="left:1016px" width="26" height="56" viewBox="0 0 26 56"><path d="M2 2 L23 28 L2 54" fill="none" stroke="#777" stroke-width="2"/></svg>
  <p class="quote"><b>“</b> We were introduced to Kelvanbrook when we needed to integrate with one of our vendors, Kelvanbrook working for our vendor, they were fast and responsive compared to our existing IT provider. It opened our eyes and now we use Kelvanbrook for all our technology needs <b>”</b></p>
  <p class="author">-By Author Name</p>
</section>

<section class="contact">
  <h2>QUICK CONTACT FORM</h2>
  <div class="field" style="left:153px;top:116px;width:221px;height:40px">First Name</div>
  <div class="field" style="left:387px;top:116px;width:214px;height:40px">Last Name</div>
  <div class="field" style="left:616px;top:116px;width:215px;height:40px">Email address</div>
  <div class="field" style="left:839px;top:116px;width:221px;height:40px">Phone</div>
  <div class="field" style="left:153px;top:164px;width:907px;height:79px">Message</div>
  <div class="btn">Submit</div>
</section>

<section class="partners" aria-label="Technology partners">
  <div class="badge" style="left:137px;width:150px"></div>
  <div class="badge" style="left:318px;width:96px"></div>
  <div class="badge" style="left:443px;width:58px;border-radius:50%;height:58px;top:52px"></div>
  <div class="badge" style="left:545px;width:74px;height:62px;top:50px"></div>
  <div class="badge" style="left:660px;width:117px"></div>
  <div class="badge" style="left:812px;width:117px"></div>
  <div class="badge" style="left:961px;width:116px"></div>
</section>

<footer class="footer">
  <div class="fcol" style="left:153px"><h4>Company</h4><ul><li>Home</li><li>About Us</li><li>Our Services</li><li>Why Us</li><li>Contact</li></ul></div>
  <div class="fcol" style="left:358px"><h4>Resources</h4><ul><li>Support</li><li>Solutions</li><li>Clients</li><li>Testimonials</li></ul></div>
  <div class="fcol" style="left:564px"><h4>Contact Info</h4><ul><li>415 Meridian Park Drive Suite B20</li><li>Fairhaven, PA 19340</li><li>(555) 014-2290</li><li>info@kelvanbrook.com</li></ul></div>
  <div class="fcol" style="left:848px"><h4>Follow Us</h4><div class="social"><span></span><span></span><span></span><span></span></div></div>
  <div class="rule"></div>
  <p class="copy">© 2017 Company Name. All rights reserved. Term of Use</p>
</footer>

</body>
</html>
```